FinTech company looking to revamp and expand client-facing interface for our financial models

Pellworth Engines currently has a very simple website that allows clients to interact with our financial models. We are looking to completely redesign the current site and add several extra pages to provide extra functionality. We want the design to have a modern, slick feel, that will work on both a desktop or a tablet. It should be straightforward for clients to move between different pages at any time, and clear from the layout how to interact with the more advanced features. We have included screenshots of existing pages in the attached design brief, as well as sketches of the functionality required by the new pages, but can't provide a direct link to the current site.
Target Market(s)
Professional investors that will be paying to access the interface
Industry/Entity Type
Finance
Number of Pages Required
4 page
Colors
Designer to choose colors to be used in the design.
Look and feel
Each slider illustrates characteristics of the customer's brand and the style your logo design should communicate.

```html
<!DOCTYPE html>
<html lang="en">
<head>
<meta charset="utf-8">
<title>Pellworth Engines — Portfolio</title>
<link href="https://fonts.googleapis.com/css2?family=Montserrat:wght@500;600;700&family=Roboto+Condensed:wght@400&display=swap" rel="stylesheet">
<style>
:root{
  --frame:#e6e6e6;
  --white:#ffffff;
  --ink:#111111;
  --navy:#0b2f63;
  --teal:#1d6e63;
  --teal-btn:#1a6a60;
  --dark:#1e1e1e;
  --page:#f1f1f1;
  --row-alt:#efefef;
  --red:#b3262b;
  --green:#2e8b2e;
  --scrim:rgba(38,38,38,.86);
  --blue-dot:#2a57b8;
  --yellow-dot:#c9c43a;
}
*{box-sizing:border-box;margin:0;padding:0}
html,body{width:1169px;height:1200px;overflow:hidden;background:var(--frame)}
.stage{position:absolute;left:0;top:0;width:1300px;height:1335px;transform:scale(.8992);transform-origin:0 0;font-family:'Montserrat',sans-serif;color:var(--ink)}
.abs{position:absolute}
.nav{left:15px;top:15px;width:1270px;height:60px;background:var(--white);display:flex;font-weight:700;font-size:15px}
.nav .cell{display:flex;align-items:center;justify-content:center;border-right:1px solid #e4e4e4;gap:8px;font-size:14px}
.nav .brand{width:180px;font-size:18px}
.nav .active{background:var(--navy);color:#fff}
.page{left:15px;top:75px;width:1270px;height:1245px;background:#dcdcdc}
.panel{background:var(--page)}
.cond{font-family:'Roboto Condensed',sans-serif}
.scrim{left:15px;top:75px;width:1270px;height:1245px;background:var(--scrim)}
.modal{left:370px;top:150px;width:560px;height:670px;background:var(--white)}
.modal-head{height:50px;background:var(--dark);color:#fff;font-weight:600;font-size:17px;display:flex;align-items:center;justify-content:center;padding-top:2px}
.field-row{position:absolute;left:0;width:560px;height:50px;display:flex;align-items:center;border-bottom:1px solid #eee}
.field-label{width:192px;padding-left:28px;font-weight:600;font-size:16px}
.input{width:228px;height:32px;border:1px solid #bbb;border-radius:3px;font-size:15px;font-weight:500;padding-left:12px;display:flex;align-items:center;justify-content:space-between;padding-right:10px}
.btn-search{margin-left:10px;width:104px;height:30px;background:var(--teal-btn);color:#fff;font-weight:700;font-size:15px;display:flex;align-items:center;justify-content:center;border-radius:2px;box-shadow:0 1px 2px rgba(0,0,0,.4)}
.results-title{position:absolute;top:205px;width:100%;text-align:center;font-weight:600;font-size:17px}
.results{position:absolute;top:250px;left:0;width:520px;height:350px;border-top:1px solid #eee}
.result{height:70px;display:flex;align-items:center;padding-left:48px;font-size:18px}
.result:nth-child(even){background:var(--row-alt)}
.result .name{margin-left:20px;width:330px}
.check{width:24px;height:24px;border:1px solid #bbb;border-radius:4px;background:#fff;box-shadow:inset 0 2px 3px rgba(0,0,0,.08)}
.scroll{position:absolute;left:520px;top:250px;width:40px;height:350px;background:#cfcfcf}
.scroll .track{position:absolute;left:11px;top:25px;width:18px;height:300px;background:#fff;border-radius:9px}
.scroll .thumb{position:absolute;left:11px;top:25px;width:18px;height:74px;background:#9a9a9a;border-radius:9px}
.modal-foot{position:absolute;top:600px;width:100%;height:70px;background:#f3f3f3;display:flex;align-items:center;justify-content:center}
.btn-add{width:170px;height:40px;background:var(--navy);color:#fff;font-weight:700;font-size:14px;display:flex;align-items:center;justify-content:center;gap:9px;border-radius:2px}
.member-row{position:absolute;left:70px;width:560px;height:69px;display:flex;align-items:center;padding-left:50px;font-size:18px;color:#444;border-bottom:1px solid #ddd}
.tab{position:absolute;top:865px;height:35px;font-size:14px;display:flex;align-items:center;justify-content:center;color:#555}
</style>
</head>
<body>
<div class="stage">
  <nav class="nav abs">
    <div class="cell brand">QORVEX</div>
    <div class="cell" style="width:90px">250D</div>
    <div class="cell" style="width:90px">83D</div>
    <div class="cell" style="width:90px">42D</div>
    <div class="cell" style="width:135px"></div>
    <div class="cell" style="width:140px;border-left:1px solid #e4e4e4">
      <svg width="26" height="24" viewBox="0 0 26 24"><path d="M2 12 13 2l11 10h-3v10h-6v-7h-4v7H5V12z" fill="#111"/></svg>MODELS</div>
    <div class="cell" style="width:177px">
      <svg width="26" height="26" viewBox="0 0 26 26" fill="#111"><circle cx="13" cy="13" r="3"/><g><circle cx="13" cy="3" r="2"/><circle cx="13" cy="23" r="2"/><circle cx="3" cy="13" r="2"/><circle cx="23" cy="13" r="2"/><circle cx="6" cy="6" r="2"/><circle cx="20" cy="20" r="2"/><circle cx="20" cy="6" r="2"/><circle cx="6" cy="20" r="2"/></g></svg>SENSITIVITIES</div>
    <div class="cell active" style="width:161px">
      <svg width="24" height="24" viewBox="0 0 24 24" fill="none" stroke="#fff" stroke-width="2"><circle cx="6" cy="6" r="4"/><circle cx="18" cy="6" r="4"/><circle cx="6" cy="18" r="4"/><circle cx="18" cy="18" r="4"/></svg>PORTFOLIO</div>
    <div class="cell" style="width:151px">
      <svg width="26" height="22" viewBox="0 0 26 22" fill="none" stroke="#111" stroke-width="2"><rect x="1" y="1" width="24" height="20"/><path d="M4 16 9 9l4 5 4-7 5 5"/></svg>BACKTEST</div>
  </nav>

  <div class="page abs">
    <div class="abs panel" style="left:55px;top:40px;width:560px;height:515px">
      <div style="height:50px;background:#222;color:#eee;font-weight:600;font-size:17px;text-align:center;line-height:50px">Current Members</div>
      <div style="height:50px;background:var(--teal);color:#ddd;font-weight:600;font-size:16px;line-height:50px;padding-left:60px">Members Name</div>
    </div>
    <div class="abs panel" style="left:655px;top:40px;width:560px;height:350px">
      <div style="height:70px;background:var(--teal);color:#ddd;font-weight:600;font-size:17px;text-align:center;line-height:70px">Sensitivities</div>
      <div class="abs" style="left:375px;top:88px;width:68px;height:36px;background:var(--green)"></div>
      <div class="abs cond" style="left:455px;top:92px;font-size:18px">0.9</div>
      <div class="abs" style="left:375px;top:158px;width:54px;height:36px;background:var(--green)"></div>
      <div class="abs cond" style="left:441px;top:162px;font-size:18px">0.7</div>
      <div class="abs" style="left:335px;top:228px;width:40px;height:36px;background:var(--red)"></div>
      <div class="abs cond" style="left:298px;top:234px;font-size:16px">-0.6</div>
      <div class="abs" style="left:355px;top:298px;width:20px;height:36px;background:var(--red)"></div>
      <div class="abs cond" style="left:318px;top:304px;font-size:16px">-0.3</div>
    </div>
    <div class="abs" style="left:55px;top:580px;width:168px;height:40px;background:var(--navy);color:#fff;font-size:14px;font-weight:700;line-height:40px;padding-left:45px">ADD A MEMBER</div>
    <div class="abs" style="left:235px;top:580px;width:170px;height:40px;background:var(--green);color:#fff;font-size:14px;font-weight:700;line-height:40px;padding-left:43px">SAVE PORTFOLIO</div>
    <div class="abs panel" style="left:55px;top:735px;width:1160px;height:430px"></div>
  </div>
  <div class="member-row cond" style="top:218px">Member 1</div>
  <div class="member-row cond" style="top:287px">Member 2</div>
  <div class="member-row cond" style="top:356px">Member 3</div>
  <div class="member-row cond" style="top:425px">Member 4</div>
  <div class="member-row cond" style="top:494px">Member 5</div>
  <div class="member-row cond" style="top:563px">Member 6</div>

  <div class="tab" style="left:125px;width:155px;background:var(--navy);color:#fff;font-weight:600">CHART</div>
  <div class="tab" style="left:285px;width:90px">#1</div>
  <div class="tab" style="left:380px;width:90px">#2</div>
  <div class="tab" style="left:475px;width:90px">#3</div>
  <div class="tab" style="left:570px;top:855px;width:90px;background:#111;color:#999">#4</div>

  <svg class="abs" style="left:125px;top:950px" width="1060" height="240" viewBox="0 0 1060 240" font-family="serif" font-size="12" fill="#666">
    <text x="5" y="17">100</text><text x="12" y="54">80</text><text x="12" y="92">60</text><text x="12" y="130">40</text><text x="12" y="167">20</text><text x="18" y="204">0</text>
    <line x1="25" y1="200" x2="950" y2="200" stroke="#999"/>
    <text x="35" y="226">Jul 2018</text><text x="175" y="226">Sep 2018</text><text x="315" y="226">Nov 2018</text><text x="457" y="226">Jan 2019</text><text x="592" y="226">Mar 2019</text><text x="732" y="226">May 2019</text><text x="876" y="226">Jul 2019</text>
    <text x="1007" y="16">Names</text>
    <g stroke-linecap="round" stroke-width="7" stroke-dasharray="0 7">
      <line x1="78" y1="13" x2="210" y2="13" stroke="var(--yellow-dot)"/>
      <line x1="415" y1="13" x2="460" y2="13" stroke="var(--yellow-dot)"/>
      <line x1="465" y1="13" x2="905" y2="13" stroke="var(--blue-dot)"/>
      <line x1="875" y1="196" x2="890" y2="196" stroke="var(--green)"/>
    </g>
    <g fill="var(--blue-dot)">
      <circle cx="78" cy="78" r="3.5"/><circle cx="98" cy="95" r="3.5"/><circle cx="108" cy="130" r="3.5"/><circle cx="115" cy="145" r="3.5"/><circle cx="130" cy="90" r="3.5"/><circle cx="140" cy="115" r="3.5"/><circle cx="150" cy="150" r="3.5"/><circle cx="165" cy="130" r="3.5"/><circle cx="180" cy="150" r="3.5"/><circle cx="195" cy="155" r="3.5"/><circle cx="212" cy="180" r="3.5"/><circle cx="230" cy="175" r="3.5"/><circle cx="248" cy="170" r="3.5"/><circle cx="260" cy="155" r="3.5"/><circle cx="275" cy="145" r="3.5"/><circle cx="290" cy="155" r="3.5"/><circle cx="305" cy="145" r="3.5"/><circle cx="320" cy="175" r="3.5"/><circle cx="340" cy="40" r="3.5"/><circle cx="355" cy="45" r="3.5"/><circle cx="365" cy="50" r="3.5"/><circle cx="340" cy="70" r="3.5"/><circle cx="370" cy="155" r="3.5"/><circle cx="385" cy="145" r="3.5"/><circle cx="400" cy="125" r="3.5"/><circle cx="410" cy="115" r="3.5"/><circle cx="420" cy="30" r="3.5"/><circle cx="432" cy="18" r="3.5"/><circle cx="80" cy="22" r="3.5"/><circle cx="92" cy="22" r="3.5"/><circle cx="1015" cy="197" r="3.5"/>
    </g>
    <g fill="var(--yellow-dot)">
      <circle cx="170" cy="22" r="3.5"/><circle cx="190" cy="18" r="3.5"/><circle cx="210" cy="80" r="3.5"/><circle cx="220" cy="110" r="3.5"/><circle cx="235" cy="95" r="3.5"/><circle cx="245" cy="130" r="3.5"/><circle cx="258" cy="75" r="3.5"/><circle cx="270" cy="45" r="3.5"/><circle cx="280" cy="18" r="3.5"/><circle cx="295" cy="85" r="3.5"/><circle cx="305" cy="100" r="3.5"/><circle cx="320" cy="160" r="3.5"/><circle cx="332" cy="145" r="3.5"/><circle cx="345" cy="185" r="3.5"/><circle cx="360" cy="180" r="3.5"/><circle cx="455" cy="190" r="3.5"/><circle cx="472" cy="185" r="3.5"/><circle cx="490" cy="180" r="3.5"/><circle cx="505" cy="175" r="3.5"/><circle cx="515" cy="185" r="3.5"/><circle cx="525" cy="150" r="3.5"/><circle cx="532" cy="78" r="3.5"/><circle cx="548" cy="38" r="3.5"/><circle cx="562" cy="35" r="3.5"/><circle cx="575" cy="160" r="3.5"/><circle cx="585" cy="45" r="3.5"/><circle cx="595" cy="70" r="3.5"/><circle cx="612" cy="35" r="3.5"/><circle cx="625" cy="25" r="3.5"/><circle cx="598" cy="112" r="3.5"/><circle cx="990" cy="50" r="3.5"/><circle cx="990" cy="160" r="3.5"/>
    </g>
  </svg>

  <div class="scrim abs"></div>

  <div class="modal abs">
    <div class="modal-head">Add a Member</div>
    <div class="field-row" style="top:50px">
      <div class="field-label">Search Database</div>
      <div class="input">Name</div>
      <div class="btn-search">Search</div>
    </div>
    <div class="field-row" style="top:100px">
      <div class="field-label">Filter by Sector</div>
      <div class="input">Select sector
        <svg width="16" height="9" viewBox="0 0 16 9"><path d="M0 0h16L8 9z" fill="#333"/></svg></div>
      <div class="btn-search">Search</div>
    </div>
    <div class="results-title">Search Results</div>
    <div class="results cond">
      <div class="result"><svg width="28" height="28" viewBox="0 0 28 28" fill="none" stroke="var(--red)" stroke-width="2"><circle cx="14" cy="14" r="12"/><path d="M14 8v12M8 14h12"/></svg><span class="name">Member 1</span><span class="check"></span></div>
      <div class="result"><svg width="28" height="28" viewBox="0 0 28 28" fill="none" stroke="var(--red)" stroke-width="2"><circle cx="14" cy="14" r="12"/><path d="M14 8v12M8 14h12"/></svg><span class="name">Member 2</span><span class="check"></span></div>
      <div class="result"><svg width="28" height="28" viewBox="0 0 28 28" fill="none" stroke="var(--red)" stroke-width="2"><circle cx="14" cy="14" r="12"/><path d="M14 8v12M8 14h12"/></svg><span class="name">Member 3</span><span class="check"></span></div>
      <div class="result"><svg width="28" height="28" viewBox="0 0 28 28" fill="none" stroke="var(--red)" stroke-width="2"><circle cx="14" cy="14" r="12"/><path d="M14 8v12M8 14h12"/></svg><span class="name">Member 4</span><span class="check"></span></div>
      <div class="result"><svg width="28" height="28" viewBox="0 0 28 28" fill="none" stroke="var(--red)" stroke-width="2"><circle cx="14" cy="14" r="12"/><path d="M14 8v12M8 14h12"/></svg><span class="name">Member 5</span><span class="check"></span></div>
    </div>
    <div class="scroll"><div class="track"></div><div class="thumb"></div></div>
    <div class="modal-foot">
      <div class="btn-add"><svg width="22" height="22" viewBox="0 0 22 22" fill="none" stroke="#fff" stroke-width="2"><circle cx="11" cy="11" r="9.5"/><path d="M11 6v10M6 11h10"/></svg>ADD MEMBER</div>
    </div>
  </div>
</div>
</body>
</html>
```